Velmora Battery Saver App UI design.

We need a mockup layout design of an Velmora app uncoded. This simple battery saver app is composed primarily by three screens described in the attached specification. After the mockup approved we need the UI elements sliced, the app icon and a banner for the nook mart.

```html
<!DOCTYPE html>
<html lang="en">
<head>
<meta charset="utf-8">
<title>Velmora Pro Ve Nova – Store Banner</title>
<link rel="stylesheet" href="https://fonts.googleapis.com/css2?family=Ubuntu:wght@400;500;700&display=swap">
<style>
  :root{
    --bg-dark:#0c0c0c;
    --bg-mid:#1e1e1e;
    --green:#3fe014;
    --green-deep:#2aa50a;
    --white:#f4f4f4;
    --frame:#f2f2f2;
    --screen:#161616;
    --screen-bar:#262626;
    --muted:#8a8a8a;
  }
  html,body{margin:0;padding:0;overflow:hidden;background:var(--bg-dark);}
  .banner{
    position:relative;width:1200px;height:675px;overflow:hidden;
    background:radial-gradient(ellipse at 55% 45%, var(--bg-mid) 0%, var(--bg-dark) 75%);
    font-family:"Ubuntu",sans-serif;
  }
  .banner svg{position:absolute;left:0;top:0;}
  .t-green{fill:var(--green);}
  .t-white{fill:var(--white);}
  .word{font-family:"Ubuntu",sans-serif;font-weight:500;}
  .word-bold{font-family:"Ubuntu",sans-serif;font-weight:700;}
</style>
</head>
<body>
<main class="banner">
<svg width="1200" height="675" viewBox="0 0 1200 675" xmlns="http://www.w3.org/2000/svg">
  <g class="phone phone-left">
    <rect x="105" y="78" width="110" height="498" rx="18" fill="var(--frame)"/>
    <rect x="115" y="120" width="100" height="405" fill="var(--screen)"/>
    <rect x="115" y="141" width="100" height="30" fill="var(--screen-bar)"/>
    <text x="132" y="162" class="word t-green" font-size="13">Velmora</text>
    <text x="132" y="186" class="word" font-size="8" fill="var(--muted)">HISTORY</text>
    <rect x="150" y="215" width="40" height="85" rx="8" fill="var(--green-deep)" opacity=".55" role="img" aria-label="Battery mascot illustration"/>
    <circle cx="160" cy="422" r="20" fill="#111" stroke="#2c2c2c" stroke-width="2"/>
    <circle cx="160" cy="422" r="11" fill="none" stroke="var(--green)" stroke-width="2.5"/>
  </g>
  <g class="phone phone-right">
    <rect x="430" y="82" width="109" height="500" rx="18" fill="var(--frame)"/>
    <rect x="430" y="124" width="99" height="405" fill="var(--screen)"/>
    <text x="502" y="139" class="word t-white" font-size="10">00:22</text>
    <rect x="430" y="144" width="99" height="30" fill="var(--screen-bar)"/>
    <rect x="430" y="174" width="99" height="22" fill="#1d1d1d"/>
    <circle cx="497" cy="256" r="22" fill="#111" stroke="#2c2c2c" stroke-width="2"/>
    <path d="M492 247 L502 256 L492 265" fill="none" stroke="var(--green)" stroke-width="2.5"/>
    <circle cx="497" cy="330" r="22" fill="#111" stroke="#2c2c2c" stroke-width="2"/>
    <path d="M486 325 h6 l8 -7 v24 l-8 -7 h-6 z" fill="var(--green)"/>
  </g>
  <g class="phone phone-front">
    <rect x="180" y="66" width="265" height="531" rx="22" fill="var(--frame)"/>
    <rect x="190" y="112" width="245" height="434" fill="var(--screen)"/>
    <rect x="190" y="112" width="245" height="17" fill="#0e0e0e"/>
    <text x="403" y="124" class="word t-white" font-size="10" font-weight="700">00:22</text>
    <circle cx="390" cy="120" r="4.5" fill="none" stroke="var(--white)" stroke-width="1.2"/>
    <text x="315" y="173" class="word-bold" font-size="18" text-anchor="middle"><tspan class="t-green">Velmora</tspan> <tspan class="t-white">Pro</tspan></text>
    <text x="315" y="245" class="word-bold" font-size="80" text-anchor="middle" letter-spacing="-3"><tspan class="t-green">V</tspan><tspan class="t-white">e</tspan></text>
    <circle cx="419" cy="228" r="9" fill="var(--green)"/>
    <circle cx="419" cy="228" r="3.5" fill="#111"/>
    <text x="315" y="281" class="word t-white" font-size="28" text-anchor="middle">NOVA</text>
    <text x="315" y="301" class="word" font-size="10" text-anchor="middle"><tspan class="t-green">Advanced</tspan> <tspan class="t-white">Battery Saver</tspan></text>
    <rect x="262" y="325" width="106" height="170" rx="14" fill="var(--green-deep)" opacity=".6" role="img" aria-label="Battery mascot illustration"/>
    <text x="312" y="533" class="word t-green" font-size="10" text-anchor="middle">Company <tspan class="t-white">Name</tspan></text>
    <path d="M353 516 l10 -8 l-2 12 z" fill="var(--green)"/>
    <path d="M225 563 h10 M225 567 h10 M225 571 h10" stroke="#777" stroke-width="1.2"/>
    <path d="M306 569 l6 -6 l6 6 v5 h-12 z" fill="none" stroke="#777" stroke-width="1.2"/>
    <path d="M388 567 h10 M388 567 l4 -4" stroke="#777" stroke-width="1.2" fill="none"/>
  </g>

  <g class="headline">
    <text x="838" y="205" class="word-bold" font-size="40" text-anchor="middle"><tspan class="t-green">Velmora</tspan> <tspan class="t-white" dx="4">Pro</tspan></text>
    <text x="840" y="362" class="word-bold" font-size="200" text-anchor="middle" letter-spacing="-8"><tspan class="t-green">V</tspan><tspan class="t-white">e</tspan></text>
    <text x="842" y="435" class="word t-white" font-size="60" text-anchor="middle">NOVA</text>
    <text x="838" y="478" class="word-bold" font-size="21" text-anchor="middle"><tspan class="t-green">Advanced</tspan> <tspan class="t-white">Battery Saver</tspan></text>
  </g>

  <circle class="badge" cx="1078" cy="132" r="72" fill="var(--green-deep)"/>
</svg>
</main>
</body>
</html>
```